Wordpress Design Project - Australian Solar Company wants to start FRESH!

About us

Bright Meadow are a renewable energy company based in Perth Australia, but we also have offices all over Asia. We specialise in offering renewable energy solutions (Solar PV Systems and LED Lighting) to residential and commercial customers.

Our current website: www.brightmeadowenergy.com.au

Our needs

This will be a replacement website as we are not happy with our current layout. We have an Australian company doing our SEO and they have recommended a new layout which we wish to go with.

We really want a professional and easy to navigate website that will assist in bringing in more enquiries and phone calls.

Content

We have all the content and will get the design winner to add this after we have chosen the design we like.
It is important that the call to actions are presented well and are visible these are things like the free quote form and our phone number.

The layout as we have advised has been based on SEO research so we wish it to be exactly the same unless otherwise stated.

Call to action

Our main objective of the new website is for people to come to the home page and see us as a professional and reliable company to deal with and enquire further.

We really want as many people as we can to convert to a lead. We want every person that comes to the website to enquire online or call us. We feel it is important to have a contact us/quote form on every page of the website.

Functional requirements

We have a chatterbook and vidstream account so links to these would be needed

Design assets

The logo needs to be displayed as shown in the website layout brief

Colours – we would like fresh, subdued colours that are professional and appealing to the eye. We ask that you do not take the colours from the logo.

Current website dislikes – the things we currently dislike about our current website is that it is hard to find information and there is no clear call to action. The colours are really unappealing as well as it looks cheap not professional.
The graphics that we require for the slider on the home page will have to be given after the winner is chosen but we want there to be three sliders on rotation

- Credibility builder (employee infront of solar panel) that encourages we use all our own employees not subcontractors
- Residential Slider – picture of a couple and solar panel system with a testimonial
- Commercial slider – picture of commercial system with “find out how you can install solar for free* at your business”

Design ideas

The website needs to be mobile friendly as well
It is going to be a total rebuild from the current website as our current website really isn’t working for us.

Target Market(s)

Target Audience

Our target audience are both residential and commercial clients
Residential – we want to attract home owners that are interested in reducing their electricity bill and helping the environment. Generally these people are between the ages of 28-50+ both male and female.

Commercial – We want to appeal to key decision makers within the commercial sphere. For example – CEOs, Company Directors, Operation managers and business owners of any industry. These people will be interested in reducing their electricity bills and creating a clean green image for their business.
Our target audience will generally come to our website to get information and enquire for a quote/ product information.

Industry/Entity Type

Residential

Requirements
Must have
• MUST BE LAID OUT LIKE THIS:

http://www.pagevaultdocs.com/doc/482937105/Website-Layout

Must have Enquire Now forms on every page that read:

Name
Phone Number
How did you hear about us
Message

```html
<!DOCTYPE html>
<html lang="en">
<head>
<meta charset="utf-8">
<title>Bright Meadow – Home</title>
<link rel="stylesheet" href="https://fonts.googleapis.com/css2?family=Source+Sans+3:wght@400;600;700&display=swap">
<style>
:root{
  --green:#00923f;
  --green-text:#0a9a47;
  --page:#efefef;
  --panel:#ffffff;
  --text:#5a5a5a;
  --dark:#333333;
  --orange:#f0a800;
  --sky-top:#2f63b8;
  --sky-bottom:#6fa4e4;
  --quote-bg:#f2f3f5;
  --social:#4a4a4a;
}
*{box-sizing:border-box;margin:0;padding:0}
html,body{width:1098px;height:1200px;overflow:hidden}
body{background:var(--page);font-family:"Source Sans 3",sans-serif;color:var(--text);position:relative}
.abs{position:absolute}
.site{position:absolute;left:72px;top:0;width:955px;height:1200px;background:var(--panel);border-top:5px solid var(--green)}
.brand{left:113px;top:56px}
.brand-name{font-size:28px;font-weight:600;color:var(--dark)}
.call{left:610px;top:30px;font-size:15px;color:var(--dark)}
.call b{font-weight:400;color:var(--green);font-size:20px}
.social-top{left:829px;top:30px;display:flex;gap:15px}
.social-top span{width:24px;height:24px;border-radius:50%;background:#2d6db5}
.social-top span:nth-child(2){background:#333}
.social-top span:nth-child(3){background:#2ba3e3}
.social-top span:nth-child(4){background:#1b72b5}
.nav{left:431px;top:85px;display:flex;font-size:14.5px;color:var(--dark)}
.nav a{color:inherit;text-decoration:none;margin-right:23px}
.nav a.active{color:var(--green)}
.hero{left:113px;top:138px;width:858px;height:360px;background:linear-gradient(180deg,var(--sky-top),var(--sky-bottom))}
.enquiry{left:735px;top:207px;width:216px;height:254px;background:rgba(255,255,255,.35)}
.enquiry h2{position:absolute;left:23px;top:8px;font-size:17px;font-weight:400;color:#fff}
.field{position:absolute;left:20px;width:177px;height:32px;background:#f5f5f5;border-radius:2px;font-size:12.5px;color:#777;padding:7px 7px}
.field.msg{height:52px;padding-top:4px}
.send{position:absolute;left:140px;top:223px;width:58px;height:25px;background:var(--orange);color:#fff;font-size:14px;text-align:center;line-height:25px}
.dots{left:899px;top:476px;display:flex;gap:4px}
.dots span{width:10px;height:10px;border-radius:50%;background:#e5e5e5}
.dots span:first-child{background:#777}
.card{width:193px}
.card .thumb{height:128px;border:1px solid #ddd;padding:3px}
.card .thumb div{width:100%;height:100%}
.card h3{margin-top:6px;font-size:15px;font-weight:400;color:var(--green-text)}
.card p{font-size:11.4px;line-height:18px;margin-top:1px;letter-spacing:.1px}
.more{font-size:11px;color:var(--dark);margin-top:7px;display:block}
h2.sec{font-size:17px;font-weight:400;color:var(--green-text)}
.video{left:114px;top:839px;width:188px;height:147px;border:1px solid #ddd;padding:2px}
.video div{width:100%;height:100%;background:linear-gradient(180deg,#5b84b8,#4f7a4a 70%,#3b6b2c)}
.welcome-text{left:319px;top:835px;width:320px;font-size:11.5px;line-height:18px}
.quote{left:707px;top:837px;width:262px;height:77px;background:var(--quote-bg);padding:12px 10px 0 17px;font-size:11.5px;line-height:20px}
.avatar{left:708px;top:925px;width:60px;height:57px;background:linear-gradient(180deg,#d9dde3,#c9b9a8)}
.person{left:778px;top:923px;width:190px;font-size:11px;font-weight:600;color:var(--dark);line-height:18px}
.cta{top:1026px;width:194px;height:67px;background:var(--green);color:#fff;font-size:15px;line-height:20px;display:flex;align-items:center;justify-content:space-between;padding:0 10px 0 20px}
.footer{left:72px;top:1128px;width:955px;height:72px;background:var(--page)}
.copy{left:113px;top:1142px;font-size:11.5px}
.foot-links{left:113px;top:1167px;font-size:11.5px}
.social-foot{left:711px;top:1145px;display:flex;gap:16px}
.social-foot span{width:24px;height:24px;border-radius:50%;background:var(--social)}
</style>
</head>
<body>
<div class="site"></div>

<header>
  <div class="abs brand"><span class="brand-name">Bright Meadow</span></div>
  <div class="abs call">CALL NOW : <b>+61 400 555 012</b></div>
  <div class="abs social-top" aria-label="Social links"><span></span><span></span><span></span><span></span></div>
  <nav class="abs nav">
    <a class="active" href="#">HOME</a><a href="#">ABOUT US</a><a href="#">PRODUCTS</a><a href="#">SERVICES</a><a href="#">WHY BRIGHT MEADOW</a><a href="#">CONTACT</a>
  </nav>
</header>

<section class="abs hero" role="img" aria-label="Solar panel array on a pole against a blue sky"></section>
<form class="abs enquiry">
  <h2>ENQUIRY FORM</h2>
  <div class="field" style="top:37px">Name</div>
  <div class="field" style="top:77px">Mobile No.</div>
  <div class="field" style="top:117px">How did you hear about us</div>
  <div class="field msg" style="top:159px">Message</div>
  <div class="send">SEND</div>
</form>
<div class="abs dots"><span></span><span></span><span></span><span></span></div>

<section>
  <div class="abs card" style="left:116px;top:532px">
    <div class="thumb"><div role="img" aria-label="House roof with solar panels" style="background:linear-gradient(180deg,#8fb6e0,#4a6a8a 50%,#5ea43a)"></div></div>
    <h3>RESIDENTIAL SOLAR POWER</h3>
    <p>Lorem ipsum dolor sit amet, consectet uer adipiscing elit. Mauris vel tortor vit ae nibh condimentum auctor.</p>
    <span class="more">READ MORE &nbsp;»</span>
  </div>
  <div class="abs card" style="left:337px;top:532px">
    <div class="thumb"><div role="img" aria-label="Commercial solar carport over a car park" style="background:linear-gradient(180deg,#b9d3ef,#3c6aa8 45%,#6f7377)"></div></div>
    <h3>COMMERCIAL SOLAR POWER</h3>
    <p>Lorem ipsum dolor sit amet, consectet uer adipiscing elit. Mauris vel tortor vit ae nibh condimentum auctor.</p>
    <span class="more">READ MORE &nbsp;»</span>
  </div>
  <div class="abs card" style="left:560px;top:532px">
    <div class="thumb"><div role="img" aria-label="Window air conditioning unit" style="background:linear-gradient(180deg,#f4f4f4,#cfd2d4)"></div></div>
    <h3>AIR CONDITIONING WA</h3>
    <p>Lorem ipsum dolor sit amet, consectet uer adipiscing elit. Mauris vel tortor vit ae nibh condimentum auctor.</p>
    <span class="more">READ MORE &nbsp;»</span>
  </div>
  <div class="abs card" style="left:779px;top:532px">
    <div class="thumb"><div role="img" aria-label="Assorted LED light bulbs" style="background:linear-gradient(180deg,#f2f2f2,#b8b2a6)"></div></div>
    <h3>PERTH LED LIGHTING</h3>
    <p>Lorem ipsum dolor sit amet, consectet uer adipiscing elit. Mauris vel tortor vit ae nibh condimentum auctor.</p>
    <span class="more">READ MORE &nbsp;»</span>
  </div>
</section>

<section>
  <h2 class="abs sec" style="left:112px;top:805px">Welcome to our Website</h2>
  <div class="abs video"><div role="img" aria-label="Video still of a solar tracker in a field"></div></div>
  <svg class="abs" style="left:183px;top:891px" width="40" height="40" viewBox="0 0 40 40"><circle cx="20" cy="20" r="18" fill="none" stroke="#fff" stroke-width="2.5"/><path d="M15 12 L29 20 L15 28Z" fill="#fff"/></svg>
  <p class="abs welcome-text">Lorem ipsum dolor consectetur scing elit. Phasellus eu placeirat justo. Nam vestibulum imperdiet suscipit ac tristique libero poir ta. Donec id ante magna. Nullam sollicitudin, ipsum vel hendrer it aliquam, nisi sapien pellentesque odio, sed tincidunt nibh tur pis at purus. Ut id magna mauris. Sed luctus rhoncus nisi, id luct us dui fermentum ac. In ac odio eu leo<br>Lorem ipsum dolior consectetur scing elit. Phasellus vestibulum imperdiet suscipit.</p>

  <h2 class="abs sec" style="left:713px;top:805px">Testimonials</h2>
  <blockquote class="abs quote">“Fusce feugiat malesuada odio. Morbi nunc odio gravida &nbsp;at, cursusi nec, luctus a, lorem. Maecen as tristique orci acd sem. ”</blockquote>
  <div class="abs avatar" role="img" aria-label="Customer portrait"></div>
  <div class="abs person">Maecenintty interu consequat sem cursus digni
    <div style="margin-top:7px;display:flex;align-items:center;gap:12px">
      <svg width="14" height="14" viewBox="0 0 14 14"><circle cx="7" cy="4" r="3.5" fill="#555"/><path d="M0 14 Q7 5 14 14Z" fill="#555"/></svg>Dana Morrow</div>
  </div>
</section>

<section>
  <div class="abs cta" style="left:113px"><span>Primary Products<br>/ Services</span>
    <svg width="42" height="42" viewBox="0 0 42 42"><g fill="#fff"><circle cx="21" cy="21" r="14"/><rect x="17" y="1" width="8" height="40" rx="2"/><rect x="1" y="17" width="40" height="8" rx="2"/><rect x="17" y="1" width="8" height="40" rx="2" transform="rotate(45 21 21)"/><rect x="17" y="1" width="8" height="40" rx="2" transform="rotate(-45 21 21)"/></g><circle cx="21" cy="21" r="6" fill="var(--green)"/></svg></div>
  <div class="abs cta" style="left:336px"><span>MemberShips</span>
    <svg width="52" height="46" viewBox="0 0 52 46"><g fill="#fff"><circle cx="33" cy="11" r="9"/><path d="M20 44 Q22 22 33 22 Q46 22 50 40 L50 44Z"/><circle cx="18" cy="16" r="9" stroke="var(--green)" stroke-width="2"/><path d="M2 46 Q4 27 18 27 Q32 27 34 46Z" stroke="var(--green)" stroke-width="2"/></g></svg></div>
  <div class="abs cta" style="left:558px"><span>Request<br>Quotation</span>
    <svg width="48" height="48" viewBox="0 0 48 48"><path d="M30 6 H6 V44 H42 V22" fill="none" stroke="#fff" stroke-width="4"/><path d="M38 3 L45 10 L24 31 L16 33 L18 25Z" fill="#fff"/></svg></div>
  <div class="abs cta" style="left:776px"><span>Contact<br>Information</span>
    <svg width="46" height="46" viewBox="0 0 46 46"><path d="M44 2 L2 24 L16 29 L20 44 L27 33 L38 40Z M44 2 L16 29 M44 2 L27 33" fill="none" stroke="#fff" stroke-width="2.5" stroke-linejoin="round"/></svg></div>
</section>

<footer>
  <div class="abs footer"></div>
  <p class="abs copy">Copyrights 2013. All Rights Reserved.</p>
  <p class="abs foot-links">Home | About us | Products | Services | Why Bright Meadow | Contact</p>
  <div class="abs social-foot" aria-label="Social links"><span></span><span></span><span></span><span></span><span></span></div>
</footer>
</body>
</html>
```